Website Design for Agency

We require a website for our new agency. We have created a brief with our content, copywriting and most graphical assets. We just need some great with layout and to add some flair.

Number of Pages Required

1 page

Font styles to use
Sans Serif

```html
<!DOCTYPE html>
<html lang="en">
<head>
<meta charset="utf-8">
<title>Proofline Studio</title>
<link rel="stylesheet" href="https://fonts.googleapis.com/css2?family=Poppins:wght@400;500;600;700&family=Roboto:wght@400;500&display=swap">
<style>
:root{
  --navy:#1f1a4f;
  --ink:#1b1b1f;
  --text:#3a3a40;
  --lav:#e4e3ed;
  --grey:#f0f0f0;
  --band:#ecebf1;
  --white:#ffffff;
}
*{box-sizing:border-box;margin:0;padding:0}
html,body{width:1200px;height:5357px;overflow:hidden;background:var(--white)}
body{position:relative;font-family:"Roboto",Arial,sans-serif;color:var(--text)}
.abs{position:absolute}
h1,h2,h3,.heading{font-family:"Poppins",Arial,sans-serif;color:var(--ink);font-weight:500}
.para{font-size:13.5px;line-height:26px;text-align:justify;color:var(--text)}
.btn{position:absolute;height:46px;border-radius:23px;font-family:"Poppins",Arial,sans-serif;font-size:14px;font-weight:500;display:flex;align-items:center;justify-content:center;gap:8px}
.btn-solid{background:var(--navy);color:var(--white)}
.btn-line{border:2px solid var(--navy);color:var(--navy);background:var(--white)}
.art{position:absolute;background:linear-gradient(160deg,#f7f7fa,#dcdbe6)}
.card-shadow{box-shadow:0 4px 18px rgba(0,0,0,.16);background:var(--white)}
.section{position:absolute;left:0;width:1200px}

/* header */
.brand{left:110px;top:24px;text-align:center}
.brand-name{font-family:"Poppins",Arial,sans-serif;font-weight:700;font-size:25px;color:var(--navy);letter-spacing:.5px;line-height:30px}
.brand-sub{font-size:13px;letter-spacing:8px;color:var(--ink);margin-top:4px}
.nav{left:377px;top:42px;display:flex;gap:34px;font-size:14px;color:var(--ink)}
.hero-blob{left:620px;top:-40px;width:640px;height:560px;border-radius:0 0 0 320px;background:var(--lav)}

/* logos */
.logo-card{position:absolute;top:778px;width:170px;height:80px;border-radius:6px;display:flex;align-items:center;justify-content:center;font-family:"Poppins",Arial,sans-serif;font-weight:600;font-size:17px;color:#444}
.dot{position:absolute;top:898px;width:8px;height:8px;border-radius:50%;background:#b9b8c5}

/* pricing */
.plan{position:absolute;top:4525px;width:228px;height:365px;text-align:center;font-family:"Poppins",Arial,sans-serif}
.plan .pname{margin-top:52px;font-size:14px;font-weight:500;color:var(--navy)}
.plan .price{font-size:50px;font-weight:600;color:var(--navy);margin-top:8px;line-height:60px}
.plan ul{list-style:none;margin-top:22px;font-family:"Roboto",Arial,sans-serif;font-size:13.5px;color:#666}
.plan li{line-height:33px}
.plan .btn{left:37px;width:154px;top:282px}
.plan-featured{background:var(--navy)}
.plan-featured .pname,.plan-featured .price,.plan-featured li{color:var(--white)}

/* footer */
.foot-col h4{font-family:"Poppins",Arial,sans-serif;font-size:17px;font-weight:500;color:var(--ink);margin-bottom:14px}
.foot-col li{list-style:none;font-size:13.5px;line-height:26px;color:var(--text)}
.foot-col li::before{content:"»";margin-right:10px}
.social{position:absolute;top:5196px;width:36px;height:36px;border-radius:50%;background:var(--navy)}
.bullet{display:flex;align-items:center;gap:20px;font-family:"Poppins",Arial,sans-serif;font-weight:500;font-size:16px;color:var(--ink)}
.bullet::before{content:"";width:8px;height:8px;border-radius:50%;background:var(--ink)}
</style>
</head>
<body>

<!-- header & hero -->
<div class="abs hero-blob"></div>
<div class="abs brand"><div class="brand-name">PROOFLINE</div><div class="brand-sub">STUDIO</div></div>
<nav class="abs nav"><span>Home</span><span>Services ⌄</span><span>How it works ⌄</span><span>Examples</span><span>Contact</span></nav>
<div class="btn btn-solid" style="left:932px;top:28px;width:156px">Plans &amp; Pricing</div>

<h1 class="abs" style="left:110px;top:130px;width:460px;font-size:25px;line-height:43px">Win More Hearts with Powerful Case Studies</h1>
<p class="abs para" style="left:110px;top:230px;width:478px">Testimonial Videos, written PDF's, slides, one-pagers and social media content. We create spellbinding case study stories and videos that will drive business for your revenue team . No more writing, proofing organizing videographers and time-consuming hassles. We'll handle everything 100% and deliver to you powerful marketing assets you'll be proud to share.Testimonial Videos, written PDF's, slides, one-pagers and social media content. We create spellbinding case study stories and videos that will drive business for your revenue team .</p>
<div class="btn btn-solid" style="left:110px;top:462px;width:134px">Learn more</div>
<div class="btn btn-line" style="left:260px;top:462px;width:164px"><svg width="12" height="14"><path d="M0 0L12 7L0 14Z" fill="#1f1a4f"/></svg>Watch Video</div>
<div class="art" role="img" aria-label="Line illustration of a person climbing a rising arrow chart" style="left:700px;top:150px;width:360px;height:320px;background:linear-gradient(160deg,#eceaf2,#d7d5e2);border-radius:12px"></div>

<!-- trusted -->
<div class="section" style="top:633px;height:344px;background:var(--grey)"></div>
<h2 class="abs" style="left:0;width:1200px;top:692px;text-align:center;font-size:29px">Trusted by hundreds of top companies</h2>
<div class="logo-card card-shadow" style="left:110px">Northwave</div>
<div class="logo-card card-shadow" style="left:312px">Keystone</div>
<div class="logo-card card-shadow" style="left:514px">Meridia</div>
<div class="logo-card card-shadow" style="left:716px">Harbor Health</div>
<div class="logo-card card-shadow" style="left:917px">Altura</div>
<div class="dot" style="left:568px"></div><div class="dot" style="left:584px;background:var(--navy)"></div><div class="dot" style="left:600px"></div><div class="dot" style="left:616px"></div>

<!-- capture -->
<div class="art" role="img" aria-label="Illustration of two people on a video call inside browser windows" style="left:110px;top:1060px;width:390px;height:305px;border-radius:150px 190px 150px 60px;background:linear-gradient(160deg,#e7e6ef,#d8d6e3)"></div>
<h2 class="abs" style="left:600px;top:1122px;width:480px;font-size:25px;line-height:43px">Capture results, built trust and win new business</h2>
<p class="abs para" style="left:600px;top:1232px;width:478px">Combining real-world results with social proof, one well-produced customer story with multiple marketing assets will do a LOT of the heavy lifting for your business sales...because it comes directly from the mouth of a happy human who loves what you do.</p>

<!-- more than marketing -->
<svg class="abs" style="left:0;top:1490px" width="1200" height="150" viewBox="0 0 1200 150"><path d="M0 0 H1200 V60 C1080 20 980 140 760 60 C560 0 400 120 200 70 C100 45 40 30 0 50 Z" fill="#e4e3ed"/></svg>
<h2 class="abs" style="left:0;width:1200px;top:1568px;text-align:center;font-size:29px">It's More Than Marketing</h2>
<p class="abs para" style="left:240px;top:1643px;width:720px;text-align:center">No more awful sales sheets and dull corporate announcements that tell people to spend their money without reason. Our team of award-winning journalists ensure your case studies are authentic. They're real. They're raw. They give people a reason to trust you, and, more importantly, a reason to give you their business.</p>

<!-- testimonial 1 -->
<h2 class="abs" style="left:110px;top:1902px;width:480px;font-size:25px;line-height:43px">Get a testimonial video anywhere nationwide</h2>
<p class="abs para" style="left:110px;top:2010px;width:458px">You get our team of pros to handle the outreach, the interviews, the field production (or remote) and all the editing, graphics and storytelling for a lot less than you think. Powerful, proven content that moves the needle.</p>
<div class="btn btn-solid" style="left:110px;top:2143px;width:134px">Learn more</div>
<div class="btn btn-line" style="left:260px;top:2143px;width:154px">Plans &amp; Pricing</div>
<div class="abs card-shadow" style="left:652px;top:1903px;width:436px;height:300px"></div>
<div class="art" role="img" aria-label="Illustration of two people discussing a presentation board" style="left:672px;top:1920px;width:396px;height:266px"></div>
<svg class="abs" style="left:790px;top:1998px" width="120" height="120" viewBox="0 0 120 120"><circle cx="60" cy="60" r="58" fill="#1f1a4f" opacity=".2"/><circle cx="60" cy="60" r="40" fill="#1f1a4f"/><path d="M52 46L76 60L52 74Z" fill="#fff"/></svg>

<!-- testimonial 2 band -->
<div class="section" style="top:2290px;height:515px;background:var(--grey)"></div>
<div class="abs card-shadow" style="left:157px;top:2372px;width:357px;height:358px"></div>
<div class="art" role="img" aria-label="Illustration of a team meeting around a whiteboard" style="left:177px;top:2392px;width:317px;height:318px"></div>
<h2 class="abs" style="left:632px;top:2396px;width:460px;font-size:25px;line-height:43px">Get a testimonial video anywhere nationwide</h2>
<p class="abs para" style="left:632px;top:2503px;width:458px">You get our team of pros to handle the outreach, the interviews, the field production (or remote) and all the editing, graphics and storytelling for a lot less than you think. Powerful, proven content that moves the needle.</p>
<div class="btn btn-solid" style="left:632px;top:2636px;width:134px">Learn more</div>
<div class="btn btn-line" style="left:782px;top:2636px;width:154px">Plans &amp; Pricing</div>

<!-- promo -->
<h2 class="abs" style="left:113px;top:2948px;font-size:25px;line-height:43px">Promo &amp; Sales Collateral</h2>
<p class="abs para" style="left:113px;top:3013px;width:478px">From one-sheets, slides, long, short, and ultra-short articles for your website, blog, or sales team. You are in good hands knowing the content you get back is marketing gold. All without the headaches.</p>
<div class="btn btn-solid" style="left:113px;top:3125px;width:154px">Plans &amp; Pricing</div>
<div class="art" role="img" aria-label="Illustration of two people building charts and growth graphics" style="left:668px;top:2905px;width:360px;height:340px;border-radius:170px 170px 170px 60px;background:linear-gradient(160deg,#eceaf2,#d7d5e2)"></div>

<!-- need help -->
<div class="abs card-shadow" style="left:112px;top:3330px;width:438px;height:305px"></div>
<div class="art" role="img" aria-label="Illustration of two people reviewing a numbered checklist" style="left:130px;top:3346px;width:402px;height:273px"></div>
<h2 class="abs" style="left:613px;top:3332px;width:480px;font-size:25px;line-height:43px">Need help promoting your customer story? We got you.</h2>
<p class="abs para" style="left:613px;top:3440px;width:458px">You get campaign level help from our team. Landing pages, lead capture forms, press releases &amp; PR outreach to 400+ organizations and 100,000 journalists. All done by former our in-house former reporters who know how it's done.</p>
<div class="btn btn-solid" style="left:613px;top:3573px;width:134px">Learn more</div>
<div class="btn btn-line" style="left:763px;top:3573px;width:154px">Plans &amp; Pricing</div>

<!-- stress-free -->
<div class="section" style="top:3720px;height:515px;background:var(--band)"></div>
<h2 class="abs" style="left:113px;top:3774px;width:460px;font-size:25px;line-height:43px">100% stress-free case study project management</h2>
<div class="abs bullet" style="left:113px;top:3880px">Get More for Less</div>
<p class="abs para" style="left:113px;top:3918px;width:458px">Whether you manage the marketing yourself or or have an in-house marketing manager, getting case studies done can be time consuming and costly if you don't do it right. We believe partnering with a case study expert can help your business prosper and establish itself as an industry leader.</p>
<div class="abs bullet" style="left:113px;top:4068px">Free up your schedule</div>
<div class="btn btn-solid" style="left:113px;top:4120px;width:154px">Plans &amp; Pricing</div>
<div class="art" role="img" aria-label="Illustration of two people planning at a whiteboard" style="left:680px;top:3780px;width:350px;height:350px"></div>

<!-- pricing -->
<h2 class="abs" style="left:0;width:1200px;top:4312px;text-align:center;font-size:21px;line-height:38px;font-weight:600">Everything you need is right here. Avoid the headaches over<br>case study copywriting and testimonial video production. Get in touch</h2>
<div class="btn btn-solid" style="left:522px;top:4444px;width:156px">Plans &amp; Pricing</div>

<div class="plan card-shadow" style="left:110px"><div class="pname">Basic Plan</div><div class="price">$10</div><ul><li>Lorem ipsum dolor sit amet</li><li>Lorem ipsum dolor sit amet</li><li>Lorem ipsum dolor sit amet</li></ul><div class="btn btn-line">Plans &amp; Pricing</div></div>
<div class="plan plan-featured" style="left:360px"><div class="pname">Basic Plan</div><div class="price">$10</div><ul><li>Lorem ipsum dolor sit amet</li><li>Lorem ipsum dolor sit amet</li><li>Lorem ipsum dolor sit amet</li></ul><div class="btn btn-line">Plans &amp; Pricing</div></div>
<div class="plan card-shadow" style="left:609px"><div class="pname">Basic Plan</div><div class="price">$10</div><ul><li>Lorem ipsum dolor sit amet</li><li>Lorem ipsum dolor sit amet</li><li>Lorem ipsum dolor sit amet</li></ul><div class="btn btn-line">Plans &amp; Pricing</div></div>
<div class="plan card-shadow" style="left:858px"><div class="pname">Basic Plan</div><div class="price">$10</div><ul><li>Lorem ipsum dolor sit amet</li><li>Lorem ipsum dolor sit amet</li><li>Lorem ipsum dolor sit amet</li></ul><div class="btn btn-line">Plans &amp; Pricing</div></div>

<!-- footer -->
<footer class="section" style="top:4975px;height:382px;background:var(--grey)">
  <div class="abs" style="left:110px;top:100px;text-align:center"><div class="brand-name" style="font-size:32px;line-height:38px">PROOFLINE</div><div class="brand-sub" style="font-size:15px;letter-spacing:10px">STUDIO</div></div>
  <div class="abs foot-col" style="left:432px;top:86px"><h4>Quick Links</h4><ul><li>Home</li><li>Agency Sign Up</li><li>How It Works</li><li>About</li></ul></div>
  <div class="abs foot-col" style="left:640px;top:86px"><h4>Our Company</h4><ul><li>Terms &amp; Conditions</li><li>Privacy Policy</li><li>About Us</li><li>Support</li></ul></div>
  <div class="abs foot-col" style="left:863px;top:86px;width:240px">
    <h4>Contact us</h4>
    <div style="display:flex;gap:10px;font-size:13.5px;line-height:24px"><svg width="12" height="16" viewBox="0 0 12 16" style="margin-top:4px;flex:none"><path d="M6 0a6 6 0 0 0-6 6c0 4.5 6 10 6 10s6-5.5 6-10a6 6 0 0 0-6-6z" fill="#1f1a4f"/><circle cx="6" cy="6" r="2.2" fill="#f0f0f0"/></svg><span>Lorem ipsum dolor sit amet, consectetur adipiscing</span></div>
    <div style="display:flex;gap:10px;font-size:13.5px;margin-top:20px"><svg width="14" height="14" viewBox="0 0 24 24"><path d="M6.6 10.8a15 15 0 0 0 6.6 6.6l2.2-2.2a1 1 0 0 1 1-.25 11.4 11.4 0 0 0 3.6.6 1 1 0 0 1 1 1V20a1 1 0 0 1-1 1A17 17 0 0 1 3 4a1 1 0 0 1 1-1h3.5a1 1 0 0 1 1 1c0 1.25.2 2.45.6 3.6a1 1 0 0 1-.25 1z" fill="#1f1a4f"/></svg><span>1+ (555) 010 2040</span></div>
    <div style="display:flex;gap:10px;font-size:13.5px;margin-top:26px"><svg width="15" height="12" viewBox="0 0 15 12"><rect width="15" height="12" rx="1.5" fill="#1f1a4f"/><path d="M1 1.5L7.5 6.5L14 1.5" stroke="#f0f0f0" stroke-width="1.3" fill="none"/></svg><span>info@prooflinestudio.com</span></div>
  </div>
  <div class="abs" style="left:0;width:1200px;top:322px;text-align:center;font-size:13px">©Copyrights 2022 Proofline Studio &nbsp;|&nbsp; All Rights Reserved</div>
  <div class="abs" style="left:1116px;top:326px;font-size:10px">PS1</div>
</footer>
<div class="social" style="left:111px"></div>
<div class="social" style="left:154px"></div>
<div class="social" style="left:197px"></div>
<div class="social" style="left:240px"></div>

</body>
</html>
```